Webdesign für Zahnarztpraxis
Zielgruppe
Zahnarztpraxis
Aufgabenstellung
- Klares und übersichtliches Desgin
- Nicht zu verspielt
- Informativ
- Leichte Naviagtion
- Das Design der alten Webseite soll NICHT kopiert werden
- Die Farben Blau und Grün aus dem Logo sollen sich wiederfinden
- Designbeispiele, die dem Kunden gefallen sind https://www.falkmann-ostrup-zahnarztpraxis.de/ und https://www.zahvilkorn.de/

```html
<!DOCTYPE html>
<html lang="de">
<head>
<meta charset="utf-8">
<title>Kobaltwerk Zahnpraxis</title>
<link href="https://fonts.googleapis.com/css2?family=Poppins:wght@300;400;500;600&family=Karla:wght@400;500&display=swap" rel="stylesheet">
<style>
:root{
  --green:#6cb33e;
  --blue:#1d9ad7;
  --blue-soft:#3ba8e0;
  --ink:#1c1c1c;
  --ink-soft:#3a3a3a;
  --white:#ffffff;
  --line:#9cc97a;
}
*{box-sizing:border-box;margin:0;padding:0}
html,body{width:1200px;height:2785px;overflow:hidden;background:var(--white)}
body{font-family:"Poppins",sans-serif;color:var(--ink);position:relative}
.abs{position:absolute}
/* hero */
.hero{position:absolute;left:0;top:0;width:1200px;height:536px;overflow:hidden}
.hero-photo{position:absolute;inset:0;background:linear-gradient(100deg,#e7ece9 0%,#f4f7f6 35%,#ffffff 60%,#eef3f4 100%)}
.hero-waves{position:absolute;left:0;top:0}
.brand{position:absolute;left:103px;top:40px;display:flex;align-items:center;gap:10px;font-weight:500;font-size:30px;color:var(--green)}
.brand-dot{width:28px;height:28px;border-radius:50%;background:var(--blue)}
.nav{position:absolute;top:26px;right:96px;display:flex;gap:30px;font-size:16px;font-weight:500;color:var(--ink-soft)}
.nav a{color:inherit;text-decoration:none;padding-bottom:6px}
.nav a.active{color:var(--ink);border-bottom:3px solid var(--green)}
.hero-title{position:absolute;left:100px;top:212px;font-size:32px;font-weight:600;color:var(--ink)}
.hero-sub{position:absolute;left:100px;top:256px;font-size:32px;font-weight:400;color:var(--ink-soft)}
.hero-contact{position:absolute;left:100px;color:var(--white);font-size:13px;font-weight:500;display:flex;align-items:center;gap:12px}
/* praxis */
.praxis{position:absolute;left:0;top:572px;width:769px;height:446px;background:linear-gradient(135deg,#45afe3,#2c9fd9)}
.praxis-inner{position:absolute;left:184px;top:60px;color:var(--white)}
.praxis h2{font-size:24px;font-weight:500}
.praxis .lead{font-size:15px;font-weight:300;opacity:.9;margin-top:2px}
.praxis .body{font-family:"Karla",sans-serif;font-size:15px;margin-top:30px;line-height:1.25;color:#13304a}
.btn-outline{display:inline-block;border:1.5px solid var(--white);color:var(--white);font-size:15px;font-weight:500;text-align:center}
.info-rule{position:absolute;left:847px;top:586px;width:2px;height:430px;background:var(--line)}
.info{position:absolute;left:888px;top:630px;width:260px;font-family:"Karla",sans-serif;font-size:15px;line-height:1.22;color:var(--ink)}
.info h2{font-family:"Poppins",sans-serif;font-size:24px;font-weight:500}
.info .lead{font-family:"Poppins",sans-serif;font-size:15px;font-weight:300;margin-bottom:18px}
.info p{margin-bottom:18px}
/* services */
.services-title{position:absolute;left:0;width:1200px;top:1056px;text-align:center;font-size:24px;font-weight:500}
.tile{position:absolute;width:151px;height:151px;background:var(--green);box-shadow:0 3px 5px rgba(0,0,0,.25);color:#eef7e6;font-size:15px;font-weight:300;text-align:center;line-height:1.45}
.tile svg{display:block;margin:12px auto 4px}
/* team */
.team-photo{position:absolute;left:0;top:1495px;width:642px;height:371px;background:linear-gradient(160deg,#7f9a5e 0%,#c9d6c2 40%,#eef1f3 70%,#9cab82 100%)}
.team{position:absolute;left:642px;top:1495px;width:558px;height:371px;background:var(--blue);color:var(--white)}
.team h2{position:absolute;left:60px;top:112px;font-size:24px;font-weight:500}
.team p{position:absolute;left:60px;top:150px;width:360px;font-size:15px;font-weight:300;line-height:1.5}
.team .btn-outline{position:absolute;left:60px;top:273px;width:197px;height:43px;line-height:40px}
/* labor */
.labor-text{position:absolute;left:144px;top:2014px}
.labor-text h2{font-size:24px;font-weight:500}
.labor-text p{font-size:15px;font-weight:300;margin-top:2px}
.btn-green{position:absolute;left:145px;top:2178px;width:196px;height:40px;line-height:40px;background:var(--green);color:var(--white);text-align:center;font-size:15px;font-weight:500}
.labor-photo{position:absolute;left:566px;top:1906px;width:634px;height:412px;background:linear-gradient(120deg,#eceeea 0%,#d9d6cf 40%,#8e5a5c 65%,#6f6a55 100%)}
/* footer */
.footer{position:absolute;left:0;top:2364px;width:1200px;height:363px;background:linear-gradient(90deg,#f2f5f6,#fbfbfa 50%,#f1f3f2);border-top:1px solid #c9dfe9}
.fcol{position:absolute;top:50px;font-family:"Karla",sans-serif;font-size:15px;line-height:1.22;color:var(--ink)}
.fcol h3{font-family:"Poppins",sans-serif;font-size:15px;font-weight:500;margin-bottom:26px}
.fcol p{margin-bottom:18px}
.hours{display:grid;grid-template-columns:81px auto}
.fcol a{color:var(--ink);text-decoration:underline}
.bar{position:absolute;left:0;top:2727px;width:1200px;height:58px;background:var(--blue);display:flex;justify-content:center;align-items:center;gap:26px;font-size:15px;font-weight:300;color:#dff1fb}
</style>
</head>
<body>

<header class="hero">
  <div class="hero-photo" role="img" aria-label="Heller Behandlungsraum mit Zahnarztstuhl und Regal"></div>
  <svg class="hero-waves" width="1200" height="536" viewBox="0 0 1200 536">
    <path d="M0 394 C200 470 420 500 640 496 L640 536 L0 536 Z" fill="#6cb33e"/>
    <path d="M0 394 C150 452 330 490 560 498 C760 500 950 450 1200 378 L1200 536 L0 536 Z" fill="#6cb33e"/>
    <path d="M560 500 C800 470 1000 420 1200 376 L1200 536 L520 536 Z" fill="#1d9ad7"/>
  </svg>
  <div class="brand"><span class="brand-dot"></span>Kobaltwerk</div>
  <nav class="nav">
    <a class="active">Unsere Praxis</a><a>Leistungen</a><a>Praxislabor</a><a>Team</a><a>Kontakt</a>
  </nav>
  <h1 class="hero-title">Herzlich Willkommen in unserer Praxis!</h1>
  <p class="hero-sub">Ihr Wohlbefinden ist unser Anspruch.</p>
  <div class="hero-contact" style="top:463px">
    <svg width="20" height="20" viewBox="0 0 24 24" fill="none" stroke="#fff" stroke-width="2"><path d="M5 3h4l2 5-2.5 1.5a11 11 0 0 0 6 6L16 13l5 2v4a2 2 0 0 1-2 2A16 16 0 0 1 3 5a2 2 0 0 1 2-2z"/></svg>
    03410 / 55218
  </div>
  <div class="hero-contact" style="top:500px">
    <svg width="22" height="18" viewBox="0 0 24 20" fill="none" stroke="#fff" stroke-width="2"><rect x="1" y="1" width="22" height="18"/><path d="M1 2l11 9 11-9"/></svg>
    info@zahnpraxis-kobaltwerk.de
  </div>
</header>

<section class="praxis" role="img" aria-label="Behandlungszimmer in blauer Farbfläche">
  <div class="praxis-inner">
    <h2>Unsere Praxis</h2>
    <p class="lead">Praxis &amp; Dentallabor in Birkenfelde.</p>
    <p class="body">Prävention und Individualprophylaxe in jeder Altersgruppe!<br>Zahnärztin spricht auch fließend Englisch.</p>
    <span class="btn-outline" style="margin-top:30px;width:197px;height:42px;line-height:39px">Mehr erfahren</span>
  </div>
</section>

<div class="info-rule"></div>
<aside class="info">
  <h2>Wichtige Information</h2>
  <p class="lead">für unsere Patienten</p>
  <p>in der Zeit von xx.xx.2025 - einschließlich xx.xx.2025 bleibt unsere Praxis geschlossen.</p>
  <p>Die Vertretung in dieser Zeit übernimmt Frau/Herr ...</p>
  <p>Bitte melden Sie sich im Vorfeld telefonisch an.</p>
</aside>

<h2 class="services-title">Unsere Leistungen</h2>
<svg width="0" height="0" style="position:absolute">
  <defs>
    <symbol id="tooth" viewBox="0 0 80 76">
      <path d="M22 8c-10 0-16 8-16 18 0 10 5 16 7 26 2 10 3 18 8 18 5 0 5-10 7-18 1-4 3-6 6-6s5 2 6 6c2 8 2 18 7 18 5 0 6-8 8-18 2-10 7-14 7-24" fill="none" stroke="#fff" stroke-width="4" stroke-linecap="round"/>
      <path d="M22 8c6 0 10 3 14 3 5 0 8-3 14-3" fill="none" stroke="#fff" stroke-width="4" stroke-linecap="round"/>
      <circle cx="62" cy="18" r="11" fill="#6cb33e" stroke="#fff" stroke-width="3"/>
      <path d="M62 12v12M56 18h12" stroke="#fff" stroke-width="3"/>
    </symbol>
  </defs>
</svg>

<div class="tile" style="left:103px;top:1126px"><svg width="80" height="76"><use href="#tooth"/></svg>Zahnärztliche<br>Diagnostik</div>
<div class="tile" style="left:274px;top:1122px"><svg width="80" height="76"><use href="#tooth"/></svg>Individual-<br>prophylaxe</div>
<div class="tile" style="left:438px;top:1122px"><svg width="80" height="76"><use href="#tooth"/></svg>Professionelle<br>Zahnreinigung</div>
<div class="tile" style="left:608px;top:1122px"><svg width="80" height="76"><use href="#tooth"/></svg>Konservierende<br>Zahnheilkunde</div>
<div class="tile" style="left:778px;top:1122px"><svg width="80" height="76"><use href="#tooth"/></svg>Zahnärztliche<br>Prothetik</div>
<div class="tile" style="left:948px;top:1122px"><svg width="80" height="76"><use href="#tooth"/></svg>Kieferorthopädie</div>

<div class="tile" style="left:103px;top:1304px"><svg width="80" height="76"><use href="#tooth"/></svg>Chirurgische<br>Zahnheilkunde</div>
<div class="tile" style="left:274px;top:1304px"><svg width="80" height="76"><use href="#tooth"/></svg>Ästhetische<br>Zahnheilkunde</div>
<div class="tile" style="left:438px;top:1304px"><svg width="80" height="76"><use href="#tooth"/></svg>Ganzheitliche<br>Zahnheilkunde</div>
<div class="tile" style="left:608px;top:1304px"><svg width="80" height="76"><use href="#tooth"/></svg>Kinderzahn-<br>heilkunde</div>
<div class="tile" style="left:778px;top:1304px"><svg width="80" height="76"><use href="#tooth"/></svg>Bioverträglicher<br>Zahnersatz</div>
<div class="tile" style="left:948px;top:1304px"><svg width="80" height="76" viewBox="0 0 80 76"><circle cx="34" cy="38" r="32" fill="none" stroke="#fff" stroke-width="3.5"/><path d="M18 38h32M38 26l12 12-12 12" fill="none" stroke="#fff" stroke-width="3.5" stroke-linecap="round" stroke-linejoin="round"/></svg>Mehr erfahren</div>

<div class="team-photo" role="img" aria-label="Gruppenbild des Praxisteams in weißer Kleidung im Garten"></div>
<section class="team">
  <h2>Unser Praxisteam</h2>
  <p>kompetent, herzlich und darauf fokussiert, Ihre Zahngesundheit bestmöglich zu unterstützen.</p>
  <span class="btn-outline">Mehr erfahren</span>
</section>

<section class="labor-text">
  <h2>Unser Praxislabor</h2>
  <p>Unsere Praxis verfügt über ein eigenes Praxislabor.</p>
</section>
<span class="btn-green">Mehr erfahren</span>
<div class="labor-photo" role="img" aria-label="Wartezimmer mit Stühlen und Blumengesteck im Vordergrund"></div>

<footer class="footer" role="img" aria-label="Blasser Hintergrund eines Behandlungsraums">
  <div class="fcol" style="left:96px">
    <h3>So erreichen Sie uns</h3>
    <p>Lindenallee 14<br>04812 Birkenfelde</p>
    <p>Telefon: 03410-55218<br>Fax: 03410-55219</p>
    <p>E-Mail: info@zahnpraxis-kobaltwerk.de</p>
  </div>
  <div class="fcol" style="left:479px;width:260px">
    <h3>Unsere Öffnungszeiten</h3>
    <div class="hours">
      <span>Montag:</span><span>9:00 bis 13:00 Uhr und<br>14:00 bis 19:00 Uhr</span>
      <span>Dienstag:</span><span>9:00 bis 13:00 Uhr und<br>14:00 bis 19:00 Uhr</span>
    </div>
    <p style="margin-bottom:18px">Mittwoch:&nbsp;&nbsp; 9:00 bis 14:00 Uhr<br>Donnerstag: geschlossen<br>Freitag:&nbsp;&nbsp;&nbsp;&nbsp;&nbsp;&nbsp;&nbsp; 9:00 bis 13:00 Uhr</p>
    <p>... und nach Vereinbarung</p>
    <p>Infomieren Sie sich bitte hier über Aktualisierungen auf unserem Praxis-Eintrag bei Kartendienst.</p>
  </div>
  <div class="fcol" style="left:834px;width:290px">
    <h3 style="margin-bottom:22px">Telefonzeiten</h3>
    <p>Innerhalb dieser Zeiten sind wir für Sie telefonisch erreichbar:</p>
    <p>Montag:&nbsp;&nbsp;&nbsp;&nbsp;&nbsp;&nbsp; 9:00 bis 15:00 Uhr<br>Dienstag:&nbsp;&nbsp;&nbsp;&nbsp; 9:00 bis 15:00 Uhr<br>Mittwoch:&nbsp;&nbsp;&nbsp; 9:00 bis 12:00 Uhr</p>
    <p>In dringenden Fällen wenden Sie sich bitte an zahnärtlichen Notdienst.</p>
    <p>Link 'zur Notdienstsuche' <a>https://www.notdienst-zahnportal.de/patienten/notdienstsuche/</a></p>
  </div>
</footer>

<div class="bar"><span>Impressum</span><span>Datenschutz</span><span>AGB</span></div>

</body>
</html>
```